Tides of the Lantern : Navigating past quiet harbours by Feliks Orto

Need a book cover, front, back and 3D. We would like the cover to have a digital globe that also shows blockchain/nodes. Best if it can also illustrate the idea of Tides of the lantern. Please see the pictures which I have short-listed which can be potentially used for the book cover.

The book cover should look like an expert book and I have attached some graphics that we can potentially buy and use for this book cover.

The text for the back cover is attached in the docx. Some text is not finished, please leave empty spaces for this.

Target Market(s)

Those interested in technology, blockchain, business, finance and law. The more informed readers.

Industry/Entity Type

Digital

Font styles to use
Sans Serif

Colors
31a5d6
0555a3
33a6d7
3176b5
85cae6
85acd3
cee9f5
cedeed

Requirements
Must have
• We would like you to consider the images attached here for the book design. We want it to be simple, clear and like an expert book. Please refer to the docx for the back cover text. Leave some text spaces for text not yet written.
• We require, front cover, back cover and 3D. You can do the 3D after your design is selected.
Nice to have
• The cover should be classy and timeless. It should have the blockchain / nodes. Will be great if the book cover can convey the meaning of Tides of the Lantern, through the text. eg. one of the images, look like a "Vortal" type photo, maybe the text can be somewhat Vortal like.
• You are welcome to suggest photos not attached here.
• Once we have identified the winner, we will proceed to purchase the photo for our use.
• Text can be Lato, but not necessary.
Should not have
• Too messy or too many ideas. Just a simple clear idea.

```html
<!DOCTYPE html>
<html lang="en">
<head>
<meta charset="utf-8">
<title>Tides of the Lantern — Front Cover</title>
<link rel="stylesheet" href="https://fonts.googleapis.com/css2?family=Anton&family=Lato:wght@400;700&family=Oswald:wght@700&display=swap">
<style>
  :root {
    --space-deep: #020b2c;
    --space-mid: #0a2a6e;
    --space-blue: #0555a3;
    --glow-blue: #31a5d6;
    --glow-pale: #cee9f5;
    --sub-blue: #85cae6;
    --title-white: #ffffff;
  }
  * { margin: 0; padding: 0; box-sizing: border-box; }
  html, body {
    width: 1006px;
    height: 1200px;
    overflow: hidden;
    background: #ffffff;
  }
  .cover {
    position: relative;
    width: 1006px;
    height: 1200px;
    overflow: hidden;
    background:
      radial-gradient(ellipse 70% 45% at 50% 62%, rgba(49,165,214,0.35), transparent 70%),
      linear-gradient(180deg, var(--space-deep) 0%, var(--space-mid) 45%, var(--space-blue) 70%, var(--space-deep) 100%);
  }
  .cover__title {
    position: absolute;
    top: 150px;
    left: 0;
    width: 100%;
    text-align: center;
    font-family: "Anton", "Impact", sans-serif;
    color: var(--title-white);
    text-transform: uppercase;
    line-height: 0.95;
    letter-spacing: -1px;
  }
  .cover__title-top {
    display: block;
    font-size: 132px;
  }
  .cover__title-main {
    display: block;
    font-size: 210px;
  }
  .cover__subtitle {
    position: absolute;
    top: 560px;
    left: 0;
    width: 100%;
    text-align: center;
    font-family: "Lato", sans-serif;
    font-weight: 400;
    font-size: 40px;
    color: var(--sub-blue);
    letter-spacing: 0.5px;
  }
  .cover__globe {
    position: absolute;
    left: -60px;
    top: 640px;
    width: 1126px;
    height: 620px;
    border-radius: 50% 50% 0 0 / 38% 38% 0 0;
    background:
      radial-gradient(ellipse 22% 14% at 48% 6%, var(--glow-pale) 0%, rgba(206,233,245,0.6) 35%, transparent 100%),
      radial-gradient(ellipse 80% 70% at 50% 20%, var(--glow-blue) 0%, var(--space-blue) 45%, var(--space-deep) 100%);
    box-shadow: 0 -20px 80px rgba(133,202,230,0.45);
  }
  .cover__author {
    position: absolute;
    bottom: 60px;
    left: 0;
    width: 100%;
    text-align: center;
    font-family: "Oswald", sans-serif;
    font-weight: 700;
    font-size: 58px;
    color: var(--title-white);
    letter-spacing: 3px;
    text-transform: uppercase;
  }
</style>
</head>
<body>
  <main class="cover">
    <h1 class="cover__title">
      <span class="cover__title-top">Tides of the</span>
      <span class="cover__title-main">Lantern</span>
    </h1>
    <p class="cover__subtitle">Navigating past quiet harbours</p>
    <div class="cover__globe" role="img" aria-label="Glowing digital globe seen from space with networked nodes and a bright sunrise on the horizon"></div>
    <p class="cover__author">Feliks Orto</p>
  </main>
</body>
</html>
```